At Home Pet Euthanasia - business cards & brand stationary

We already have a logo and the colors and a website. Need a business card designed that will be able to customized to multiple veterinarians who will be partnering with us. The feel needs to be compassionate, comforting with our tagline 'A Gift of Love at Home'. It will be 2 sides.
On the back our platform/partner vets will be customizing each business card with their own service areas, phone numbers, name and title. On the front, i would like to see experimentation with use of our photos, the logo, tagline and a description 'Peaceful and Compassionate At-Home Pet Euthanasia'

```html
<!DOCTYPE html>
<html lang="en">
<head>
<meta charset="utf-8">
<title>HavenPaw Business Card</title>
<link rel="stylesheet" href="https://fonts.googleapis.com/css2?family=Courgette&family=Montserrat:wght@400;600;700&family=Quicksand:wght@400;500&display=swap">
<style>
  :root {
    --bg: #2b2b2d;
    --card: #ffffff;
    --brand: #7698c1;
    --brand-dark: #6a8cb6;
    --ink: #111111;
    --photo-green: #b9cf8e;
    --photo-cream: #ece4d8;
    --photo-skin: #d8b3a1;
  }
  * { margin: 0; padding: 0; box-sizing: border-box; }
  html, body { width: 1200px; height: 1015px; overflow: hidden; }
  body {
    background: var(--bg);
    font-family: "Montserrat", Arial, sans-serif;
    position: relative;
  }
  .card {
    position: absolute;
    left: 280px;
    width: 640px;
    height: 366px;
    background: var(--card);
    overflow: hidden;
  }
  /* Front */
  .card--front { top: 100px; }
  .front__photo {
    position: absolute;
    right: 0; top: 0;
    width: 380px; height: 100%;
    background:
      radial-gradient(ellipse 60% 55% at 55% 45%, var(--photo-cream) 0%, #f1ede6 55%, transparent 80%),
      radial-gradient(ellipse 40% 40% at 70% 85%, var(--photo-skin) 0%, transparent 70%),
      linear-gradient(135deg, #e8eed8 0%, var(--photo-green) 100%);
    -webkit-mask-image: linear-gradient(90deg, transparent 0%, #000 35%);
            mask-image: linear-gradient(90deg, transparent 0%, #000 35%);
  }
  .front__headline {
    position: absolute;
    left: 56px; top: 118px;
    font-family: "Courgette", cursive;
    font-weight: 400;
    font-size: 37px;
    line-height: 44px;
    color: var(--brand);
  }
  .front__headline span { display: block; }
  .front__headline span:nth-child(2) { padding-left: 18px; }
  .front__headline span:nth-child(3) { padding-left: 36px; }
  .front__headline span:nth-child(4) { padding-left: 54px; }

  /* Back */
  .card--back { top: 556px; }
  .brand {
    position: absolute;
    left: 150px; top: 40px;
    display: flex; align-items: center; gap: 18px;
  }
  .brand__mark {
    width: 58px; height: 58px;
    border-radius: 50%;
    background: var(--brand);
  }
  .brand__name {
    font-family: "Montserrat", sans-serif;
    font-weight: 700;
    font-size: 62px;
    line-height: 1;
    color: var(--brand);
  }
  .brand__tagline {
    position: absolute;
    left: 236px; top: 114px;
    font-family: "Quicksand", sans-serif;
    font-size: 22px;
    color: var(--brand);
    letter-spacing: 0.5px;
  }
  .band {
    position: absolute;
    left: 0; top: 170px;
    width: 100%; height: 112px;
    background: var(--brand);
    color: #fff;
    display: flex; align-items: center;
  }
  .person { width: 300px; text-align: right; padding-right: 22px; }
  .person__name { font-weight: 700; font-size: 26px; letter-spacing: 0.3px; }
  .person__title { font-weight: 400; font-size: 19px; }
  .band__divider { width: 2px; height: 70px; background: #fff; }
  .contacts { list-style: none; padding-left: 22px; }
  .contacts li {
    display: flex; align-items: center; gap: 10px;
    font-size: 17px; line-height: 27px; letter-spacing: 0.3px;
  }
  .contacts svg { width: 17px; height: 17px; flex: none; }
  .address {
    position: absolute;
    left: 0; top: 282px;
    width: 100%; height: 56px;
    display: flex; align-items: center; justify-content: center;
    font-size: 21px; color: var(--ink);
  }
  .address__rule {
    position: absolute; top: 0; left: 0;
    width: 100%; height: 6px;
    background: linear-gradient(90deg, var(--brand) 0 58%, var(--card) 58% 59%, var(--brand) 59% 100%);
  }
  .footer-stripe {
    position: absolute;
    left: 0; bottom: 0;
    width: 100%; height: 14px;
    background: var(--brand-dark);
  }
</style>
</head>
<body>

<section class="card card--front">
  <div class="front__photo" role="img" aria-label="Photo of a small white fluffy dog being gently held by its owner's hands outdoors"></div>
  <h1 class="front__headline">
    <span>Peaceful and</span>
    <span>Compassionate</span>
    <span>At-Home</span>
    <span>Pet Euthanasia</span>
  </h1>
</section>

<section class="card card--back">
  <div class="brand">
    <div class="brand__mark"></div>
    <div class="brand__name">HavenPaw</div>
  </div>
  <div class="brand__tagline">A gift of love at home.</div>

  <div class="band">
    <div class="person">
      <div class="person__name">DANIEL REED</div>
      <div class="person__title">Managing Director</div>
    </div>
    <div class="band__divider"></div>
    <ul class="contacts">
      <li>
        <svg viewBox="0 0 24 24" fill="none" stroke="#fff" stroke-width="2.2" stroke-linecap="round" stroke-linejoin="round"><path d="M5 3h4l2 5-2.5 1.5a11 11 0 0 0 6 6L16 13l5 2v4a2 2 0 0 1-2 2A16 16 0 0 1 3 5a2 2 0 0 1 2-2z"/></svg>
        055-210 384 917
      </li>
      <li>
        <svg viewBox="0 0 24 24" fill="none" stroke="#fff" stroke-width="2.2" stroke-linejoin="round"><rect x="2" y="5" width="20" height="14"/><path d="M2 5l10 8 10-8"/></svg>
        hello@havenpaw.com
      </li>
      <li>
        <svg viewBox="0 0 24 24" fill="none" stroke="#fff" stroke-width="2"><circle cx="12" cy="12" r="10"/><path d="M2 12h20M12 2a15 15 0 0 1 0 20M12 2a15 15 0 0 0 0 20"/></svg>
        www.havenpaw.com
      </li>
    </ul>
  </div>

  <div class="address">
    <div class="address__rule"></div>
    421, Address line goes here 45452,Country Name
  </div>
  <div class="footer-stripe"></div>
</section>

</body>
</html>
```